"LuvaWorks" Graphic Design Project

We are a new business creating bath/ body/beauty products. We need label designs for men "Velto for Men " and women- "Velto for Women" . Since the collection called Velto will be used for both- we'd like the labels to look similar but separating the gender look- maybe by a same color variation. Our bottles are amber in color , so we like the beiges, cream, and earthy warm tones - greens- brown-orange- yellow-colors. The labels are for 8 oz amber cosmo round bottles. The height is 7.32inches and the diameter is 1.85 inches.
Our starting line will be Velto for Men ( Silk Body Wash, Silk Body Lotion and Body Mist) and the same for Velto for Women.

Target Market(s)

Our target audience is between 30 to 60 years of age. Salons and private consumers.
I am including attached sample of what was started by me.

Requirements
Must have
• We would like to incorporate the company name- LuvaWorks along with the name of the product- which will be Velto for Men or Velto for Women on each label.

On label with company name or somewhere on label we would like a tree to symbolize the beginning, but we are open to suggestions.

```html
<!DOCTYPE html>
<html lang="en">
<head>
<meta charset="utf-8">
<title>Velto for Men – Silk Body Wash label</title>
<link rel="stylesheet" href="https://fonts.googleapis.com/css2?family=Quicksand:wght@300;400;500&display=swap">
<style>
  :root {
    --green-top: #2cb673;
    --green-mid: #1f8a56;
    --green-deep: #1c3b2b;
    --charcoal: #1e1f1f;
    --ink: #111412;
    --ink-soft: #1f2522;
    --white: #ffffff;
    --grey-light: #c9cfcb;
    --panel-glass: rgba(255, 255, 255, 0.18);
    --panel-edge: rgba(255, 255, 255, 0.28);
  }
  * { margin: 0; padding: 0; box-sizing: border-box; }
  html, body { width: 954px; height: 1200px; overflow: hidden; background: var(--charcoal); }
  .label {
    position: relative;
    width: 954px;
    height: 1200px;
    overflow: hidden;
    font-family: "Quicksand", sans-serif;
    background: linear-gradient(180deg, var(--green-top) 0%, var(--green-mid) 38%, var(--green-deep) 72%, var(--charcoal) 100%);
  }
  .swirl-pattern {
    position: absolute; inset: 0;
    background:
      radial-gradient(circle at 20% 45%, rgba(255,255,255,0.07), transparent 40%),
      radial-gradient(circle at 75% 20%, rgba(255,255,255,0.08), transparent 45%),
      radial-gradient(circle at 70% 85%, rgba(255,255,255,0.06), transparent 40%);
  }
  .spine {
    position: absolute; top: 0; left: 324px; width: 97px; height: 1200px;
    background: linear-gradient(90deg, rgba(0,0,0,0.28) 0%, rgba(255,255,255,0.06) 20%, rgba(255,255,255,0.04) 80%, rgba(0,0,0,0.28) 100%);
  }
  .spine-line {
    position: absolute; top: 0; left: 361px; width: 2px; height: 1200px;
    background: rgba(0,0,0,0.45);
  }
  .spine-brand {
    position: absolute; left: 367px; top: 595px;
    transform: translate(-50%, -50%) rotate(-90deg);
    font-weight: 300; font-size: 92px; color: var(--white); white-space: nowrap; letter-spacing: 1px;
  }
  .product-name {
    position: absolute; left: 59px; top: 138px;
    font-weight: 300; font-size: 80px; line-height: 1; color: var(--white);
  }
  .product-gender {
    position: absolute; left: 59px; width: 212px; top: 225px; text-align: right;
    font-weight: 400; font-size: 21px; color: var(--white);
  }
  .product-type {
    position: absolute; left: 49px; top: 612px;
    font-weight: 400; font-size: 30px; color: var(--white);
  }
  .product-size {
    position: absolute; left: 0; width: 342px; top: 1112px; text-align: center;
    font-weight: 400; font-size: 23px; line-height: 37px; color: var(--white);
  }
  .copy {
    position: absolute; left: 448px; width: 500px; top: 94px; text-align: center;
    font-weight: 400; font-size: 21.5px; line-height: 33px; color: var(--ink);
  }
  .copy p { margin-bottom: 20px; }
  .ingredients {
    position: absolute; left: 441px; top: 554px; width: 483px; height: 419px;
    border-radius: 22px; background: var(--panel-glass); border: 1px solid var(--panel-edge);
    padding: 36px 14px 0; text-align: center;
    font-weight: 400; font-size: 17px; line-height: 25px; color: var(--ink-soft);
  }
  .maker {
    position: absolute; left: 448px; width: 490px; top: 1054px; text-align: center;
    font-weight: 400; font-size: 23px; line-height: 32px; color: var(--grey-light);
  }
</style>
</head>
<body>
<main class="label">
  <div class="swirl-pattern" role="img" aria-label="Faint decorative swirl pattern over the green background"></div>
  <div class="spine"></div>
  <div class="spine-line"></div>
  <div class="spine-brand">LuvaWorks</div>

  <h1 class="product-name">Velto</h1>
  <div class="product-gender">FOR MEN</div>
  <div class="product-type">Silk Body Wash</div>
  <div class="product-size">MADE IN USA<br>8.25 fl oz. / 244mL</div>

  <section class="copy">
    <p>Our Nourishing Silk Body Wash will engulf you in luxurious lather as it gently cleanses your delicate skin leaving it soft as silk.</p>
    <p>Directions: Apply to skin while damp with sponge or wash cloth. Rinse well.</p>
    <p>WARNINGS/CAUTIONS: For external use only. Avoid contact with eyes.</p>
    <p>NOT TESTED ON ANIMALS</p>
  </section>

  <section class="ingredients">
    INGREDIENTS: purified water, sodium olefin sulfonate (plant source), organic aloe barbadensis leaf juice, cocamidopropyl betaine (plant source), sodium chloride (salt), kosher vegetable glycerin, tocopherol (natural vitamin E), polysorbate 20 (plant source), potassium sorbate (plant source), phenoxyethanol (mild preservative), caprylyl glycol (plant source), organic anthemis nobilis (chamomile) extract, organic calendula officinalis flower extract, xanthan gum (plant source), magnesium ascorbyl phosphate (vitamin C ester), sodium bicarbonate (baking soda), citric acid fragrance.
  </section>

  <footer class="maker">
    LuvaWorks<br>
    Bath – Body - Home<br>
    Coral Ridge, FL 33010<br>
    Shop 24/7 - www.luvaworks-shop.com
  </footer>
</main>
</body>
</html>
```